Modernize Website: marcusfellwright.net

I am a novelist with an older-generation website at: marcusfellwright.net.

I am hoping to refresh this outdated website with a new, responsive redesign. I would prefer to host the code myself, and edit using Arvex Dreamweaver. So I’m not looking to use a hosted site builder like Plexo. Nor am I looking to use a CMS like Pagecraft.

In order to simplify the old site, there are a number of sections I’ll be looking to remove during this redesign. These are shown in the "MF Site Redesign" attachment. I can also provide imagery for new content (another book series in addition to the existing one), as well as higher-resolution imagery (if needed) of the old content.

Happy to answer any further questions.
Updates

I've uploaded a ZIP file containing high-res artwork associated with the new trilogy of books.

Target Market(s)

Readers of epic fantasy novels such as H.W.B. Castellane's THE WARDEN OF THE VALES, Harold P.Q. Ventris's A CROWN OF ASH AND RAIN, Victor Halloway's THE GATE OF STARS, or Dennis Vale's BLADE OF MERIVANE.

Industry/Entity Type

Entertainment

Coding

Coded - Design and coding required

Number of Pages Required

5+ page

Font styles to use
Serif
Decorative

Colors

Designer to choose colors to be used in the design.

Requirements
Must have
• I'm looking for a responsive design that displays nicely on both mobile and desktop devices. Existing site contains multiple pages, but these can obviously be combined into fewer pages (or even one) by divisions such as tabs, sections, and/or modal windows. See marcusfellwright.net for current content and "MF Site Redesign" attachment for content to be removed at this time.
Nice to have
• The ability to fulfill orders of autographed books directly from the website. I currently use Coinlo to do this, but it would be nice to incorporate a more comprehensive merchant service at a reasonable rate.
Should not have
• I'd like to host and control the site code myself. So please don't use a hosted web builder like Plexo, or a cloud-based CMS like Pagecraft.

```html
<!DOCTYPE html>
<html lang="en">
<head>
<meta charset="utf-8">
<title>World – Characters | Marcus Fellwright</title>
<link rel="stylesheet" href="https://fonts.googleapis.com/css2?family=Cinzel:wght@400;700&family=Roboto:ital,wght@0,400;0,500;0,700;1,400&display=swap">
<style>
  :root{
    --black:#000000;
    --night:#0f0e13;
    --white:#ffffff;
    --soft:#e4e2e6;
    --red:#d0001a;
    --red-deep:#8a0010;
  }
  *{box-sizing:border-box;margin:0;padding:0}
  html,body{width:1200px;height:2384px;overflow:hidden}
  body{position:relative;background:var(--night);color:var(--white);font-family:"Roboto",Arial,sans-serif}

  .site-header{position:absolute;top:0;left:0;width:1200px;height:121px;background:var(--black);z-index:5}
  .brand{position:absolute;left:99px;top:28px;display:flex;flex-direction:column;gap:6px}
  .brand-name{display:flex;align-items:center;gap:10px;font-family:"Cinzel",Georgia,serif;font-weight:400;font-size:22px;color:var(--white);letter-spacing:1px}
  .brand-mark{width:12px;height:12px;background:var(--red)}
  .brand-series{font-family:"Cinzel",Georgia,serif;font-size:11px;color:var(--red);letter-spacing:1px;padding-left:80px}

  .main-nav{position:absolute;top:63px;left:529px;font-size:15px;font-weight:500}
  .main-nav a{color:var(--white);text-decoration:none;position:absolute;white-space:nowrap}
  .main-nav .caret{display:inline-block;width:6px;height:6px;border-right:1.5px solid var(--white);border-bottom:1.5px solid var(--white);transform:rotate(45deg);margin-left:6px;position:relative;top:-3px}
  .login{position:absolute;left:990px;top:59px;width:110px;height:34px;border-radius:17px;background:linear-gradient(#e0102a,#a8000f);color:var(--white);font-size:15px;font-weight:500;display:flex;align-items:center;justify-content:center;gap:7px;text-decoration:none}

  .dropdown{position:absolute;left:696px;top:121px;width:157px;height:194px;background:var(--black);z-index:6;font-size:15px;font-weight:500}
  .dropdown a{position:absolute;left:22px;color:var(--white);text-decoration:none}
  .dropdown .active{left:0;width:157px;height:38px;padding-left:22px;display:flex;align-items:center;background:linear-gradient(#e2102b,#9a000f)}

  .hero{position:absolute;top:121px;left:0;width:1200px;height:540px;background:
    radial-gradient(ellipse at 70% 40%,rgba(190,170,150,.55),transparent 55%),
    radial-gradient(ellipse at 15% 60%,rgba(120,110,100,.6),transparent 45%),
    linear-gradient(180deg,#5c5052 0%,#8a7a72 40%,#4e4246 75%,var(--night) 100%)}
  .hero-title{position:absolute;left:111px;top:295px;font-family:"Cinzel",Georgia,serif;font-weight:700;font-size:88px;color:var(--white);text-shadow:0 0 14px var(--red),0 0 26px var(--red-deep);z-index:2}

  .backdrop{position:absolute;top:661px;left:0;width:1200px;height:1344px;background:
    radial-gradient(ellipse 420px 70px at 260px 490px,rgba(180,40,20,.35),transparent),
    radial-gradient(ellipse 520px 90px at 820px 720px,rgba(190,60,30,.3),transparent),
    radial-gradient(circle 60px at 500px 640px,rgba(240,200,160,.35),transparent),
    radial-gradient(ellipse 500px 220px at 560px 1290px,rgba(90,50,40,.45),transparent),
    var(--night)}

  .content{position:absolute;left:105px;top:732px;width:960px;z-index:2}
  .page-title{font-family:"Cinzel",Georgia,serif;font-weight:700;font-size:56px;letter-spacing:0;line-height:1}
  .intro{margin-top:46px;font-size:14.5px;line-height:26px;color:var(--soft);width:920px}
  .intro a{color:var(--red)}
  .note{margin-top:21px;font-size:14.5px;color:var(--soft)}

  .glossary{list-style:none;margin-top:50px;display:flex;flex-direction:column;gap:19px}
  .glossary li{position:relative;padding-left:44px;font-size:14.5px;line-height:21px;color:var(--soft);width:960px}
  .glossary li::before{content:"";position:absolute;left:1px;top:2px;width:0;height:0;border-left:16px solid var(--red);border-top:9px solid transparent;border-bottom:9px solid transparent}
  .glossary li::after{content:"";position:absolute;left:4px;top:7px;width:0;height:0;border-left:7px solid var(--night);border-top:4px solid transparent;border-bottom:4px solid transparent}
  .glossary b{font-size:17px;font-weight:500;color:var(--white)}

  .pager{position:absolute;left:105px;top:1880px;display:flex;gap:10px;align-items:center;font-style:italic;font-size:28px;color:var(--white);z-index:2}

  .site-footer{position:absolute;top:2005px;left:0;width:1200px;height:379px;background:var(--black)}
  .footer-brand{position:absolute;left:0;width:1200px;top:80px;display:flex;flex-direction:column;align-items:center;gap:6px}
  .social{position:absolute;top:172px;left:516px;display:flex;gap:13px}
  .social a{width:49px;height:49px;border-radius:50%;background:var(--white);display:block}
  .footer-nav{position:absolute;top:264px;left:0;width:1200px;display:flex;justify-content:center;gap:24px;font-size:14px}
  .footer-nav a,.legal a{color:var(--white);text-decoration:none}
  .legal{position:absolute;top:2308px;left:0;width:1200px;display:flex;justify-content:center;gap:14px;font-size:13.5px}
  .build{position:absolute;top:2308px;left:1152px;font-size:13px}
</style>
</head>
<body>
  <header class="site-header">
    <div class="brand">
      <span class="brand-name"><span class="brand-mark"></span>Marcus Fellwright</span>
      <span class="brand-series">The Legend of Veyrandel</span>
    </div>
    <nav class="main-nav">
      <a href="#" style="left:0">HOME</a>
      <a href="#" style="left:72px">NOVELS<span class="caret"></span></a>
      <a href="#" style="left:170px">WORLD<span class="caret"></span></a>
      <a href="#" style="left:264px">AUTHOR<span class="caret"></span></a>
      <a href="#" style="left:366px">CONTACT</a>
    </nav>
    <a class="login" href="#">
      <svg width="11" height="13" viewBox="0 0 11 13" aria-hidden="true"><rect x="0" y="5" width="11" height="8" rx="1" fill="#fff"/><path d="M2.5 5V3.5a3 3 0 0 1 6 0V5" stroke="#fff" stroke-width="1.6" fill="none"/></svg>
      LOGIN
    </a>
  </header>

  <nav class="dropdown">
    <a href="#" style="top:14px">Map</a>
    <a href="#" class="active" style="top:46px">Characters</a>
    <a href="#" style="top:98px">Locations</a>
    <a href="#" style="top:128px">Artifacts</a>
    <a href="#" style="top:160px">Gallery</a>
  </nav>

  <section class="hero" role="img" aria-label="Fantasy scene: a ruined stone tower and a cloaked figure facing a winged dragon under a stormy sky"></section>
  <h1 class="hero-title">WORLD</h1>

  <div class="backdrop" role="img" aria-label="Dark starfield with glowing red meteors streaking across"></div>

  <main class="content">
    <h2 class="page-title">CHARACTERS</h2>
    <p class="intro">Below is a complete glossary of characters found throughout the "Veyrandel" books. Click the button to hear an audio pronunciation provided by <a href="#">Walter Fellwright</a> (requires Arvex's free <a href="#">Pulse Player</a> plug-in).</p>
    <p class="note">Note: Spoiler material in black text. Highlight to read.</p>

    <ul class="glossary">
      <li><b>Aberwyn</b> - Seafaring Tolvari'essan clan at feud with the Morrith.</li>
      <li><b>Adrevan</b> - In Kelmish legend, the First Forger, shaper of the mountains and their peoples.</li>
      <li><b>Aldren</b> - A Kelmish miner; father of Ossik.</li>
      <li><b>Amberlaine</b> - Mother of Serith and a retired Warden. Longtime ally to Dorvald, lord of the Kelmish.</li>
      <li><b>Ansel</b> - A Kelmish miner; youngest of Aldren.</li>
      <li><b>Arvos</b> - A Warden of Greymoor.</li>
      <li><b>Astorel</b> - An exiled Warden; forebear to Calvane.</li>
      <li><b>Athric</b> - A trapper and tracker of the hamlet Wend. [Highlight]: Later marshal (Vessan) of the Tower Guard of Harrowmere; rules as steward in the absence of the queen.</li>
      <li><b>Avenna</b> - A river spirit warden; sister-kin to Lisset.</li>
      <li><b>Aveline Darrowmir</b> - Niece of Corissa; great-niece of Lord Tamsel.</li>
      <li><b>Ayl</b> - A sellsword from the isles of Quoran.</li>
      <li><b>Azrel</b> - A Councillor of the High Council of Harrowmere. Conspirator with Malric Voss.</li>
      <li><b>Azwin</b> - A guardsman of the Tower Guard of Harrowmere; member of a voyage to Quoran.</li>
      <li><b>Baldric</b> - A baron of Ostravel.</li>
      <li><b>Banner of the Dawn</b> - A stowaway and later first mate to the smuggler queen Grey Heron.</li>
      <li><b>Barrowen</b> - Queen of Thessane who forged the Pact of the Realms; principal author of the Charter of Realms, which split Vardos north and south into the lands of Ember and Helvane and began the Age of Realms (Year 0 AR).</li>
      <li><b>Bastien</b> - Field Marshal, Fourth Company, joined Emberan Host.</li>
      <li><b>Bellan</b> - Third Elder of the hamlet Wend.</li>
      <li><b>Beron</b> - A lancer corporal and mounted patrol leader of the Emberan Host.</li>
      <li><b>Brannoc</b> - A rebel captain and North Flank leader of the Eastern Freedom Army of Thornmarch.</li>
    </ul>
  </main>

  <nav class="pager" aria-label="Pages">
    <span>1</span><span>2</span><span>3</span><span>4</span><span>5</span><span>6</span>
    <svg width="30" height="16" viewBox="0 0 30 16" aria-hidden="true"><path d="M0 8h26M19 1l8 7-8 7" stroke="#fff" stroke-width="3" fill="none"/></svg>
  </nav>

  <footer class="site-footer">
    <div class="footer-brand">
      <span class="brand-name"><span class="brand-mark"></span>Marcus Fellwright</span>
      <span class="brand-series" style="padding-left:60px">The Legend of Veyrandel</span>
    </div>
    <div class="social">
      <a href="#" aria-label="Social profile"></a>
      <a href="#" aria-label="Social feed"></a>
      <a href="#" aria-label="Email"></a>
    </div>
    <nav class="footer-nav">
      <a href="#">Home</a><span>|</span>
      <a href="#">Novels</a><span>|</span>
      <a href="#">World</a><span>|</span>
      <a href="#">Author</a><span>|</span>
      <a href="#">Contact</a>
    </nav>
  </footer>
  <div class="legal">
    <span>© Copyright 2018 Marcus Fellwright. All Rights Reserved</span><span>|</span>
    <a href="#">Terms of Use</a><span>|</span>
    <a href="#">Privacy Policy.</a>
  </div>
  <span class="build">C10</span>
</body>
</html>
```